Coastal Learner Bureau business cards

Australian company about to start offering its services. We recruit international students to come to study English, vocational education and postgraduate courses in Australia. We help them find the institution and select the right city they want to come to Australia. We are a young, online oriented and supportive agency. Our clients are between 18 and 35 years old, mainly University students, young professionals or people with work experience. We provide much more information that any other agency offer. We administrate a Facebook group with more than 11.000 members that daily ask questions about general information when coming to Australia, while they are here and even after they leave the country

Target Market(s)

International students from South America, Central America and Europe

Industry/Entity Type

Student

Contact Information for Business Card

Tomas Bilbrea
Managing Director
tomas@kelvarin.com.au
www.kelvoria.com.au
+61 491058264
Melbourne, Australia

Font styles to use
Serif
Sans Serif

Colors

Designer to choose colors to be used in the design.

Requirements
Must have
• Horizontal design
• Standard business card size and shape. If font uses green or yellow colours, they will have to match the ones from the logo
Nice to have
• UPDATE: Use the contents of the green image to design one of the card sides. Use our logo in the background of that side as watermark.
• Passport image, or immigration stamps. A picture of the Yarra River (from Melbourne) would be cool as well.
Should not have
• Non-standard business card size and shape
• Not black as the background colour of any sides as we are not a VIP agency or a hight class service. We are orientes to young people and they like colours, pictures, something attractive.
• Vertical design
• NO YELLOW or BLACK AS THE BACKGROUND COLOUR OF ANY SIDE OF THE BIZ CARD

```html
<!DOCTYPE html>
<html lang="en">
<head>
<meta charset="utf-8">
<title>Coastal Learner Bureau business cards</title>
<link rel="stylesheet" href="https://fonts.googleapis.com/css2?family=Roboto:wght@400;500;700&display=swap">
<style>
  :root {
    --backdrop: #2b2b2b;
    --paper: #f2f2f2;
    --brand-green: #105d3e;
    --brand-yellow: #d8b112;
    --white: #ffffff;
  }
  * { margin: 0; padding: 0; box-sizing: border-box; }
  html, body { width: 1200px; height: 960px; overflow: hidden; }
  body {
    background: var(--backdrop);
    font-family: "Roboto", Arial, sans-serif;
    position: relative;
  }
  .card {
    position: absolute;
    width: 600px;
    height: 343px;
    overflow: hidden;
  }
  .card--front { left: 314px; top: 113px; background: var(--paper); }
  .card--back { left: 311px; top: 472px; background: var(--brand-green); }

  .accent-bar {
    position: absolute;
    left: 0; top: 85px;
    width: 15px; height: 172px;
    background: var(--brand-yellow);
  }
  .wordmark {
    position: absolute;
    display: flex;
    align-items: center;
    gap: 10px;
    font-weight: 700;
    letter-spacing: 0.5px;
  }
  .wordmark__dot { border-radius: 50%; background: var(--brand-yellow); }
  .card--front .wordmark {
    left: 76px; top: 145px;
    font-size: 44px;
    color: var(--brand-green);
  }
  .card--front .wordmark__dot { width: 16px; height: 16px; }
  .card--back .wordmark {
    left: 170px; top: 120px;
    font-size: 62px;
    color: var(--white);
  }
  .card--back .wordmark__dot { width: 22px; height: 22px; }

  .contact-panel {
    position: absolute;
    left: 341px; top: 85px;
    width: 259px; height: 172px;
    background: var(--brand-green);
    padding: 20px 0 0 25px;
    color: var(--white);
  }
  .contact-panel__name {
    font-size: 20px;
    font-weight: 500;
    color: var(--brand-yellow);
    letter-spacing: 0.3px;
    line-height: 24px;
  }
  .contact-panel__role {
    font-size: 15.5px;
    font-weight: 500;
    letter-spacing: 0.3px;
    line-height: 20px;
    margin-bottom: 9px;
  }
  .contact-list { list-style: none; }
  .contact-list li {
    display: flex;
    align-items: center;
    gap: 8px;
    font-size: 14.5px;
    line-height: 20px;
  }
  .contact-list svg { width: 13px; height: 13px; fill: var(--brand-yellow); flex: none; }

  .tagline-band {
    position: absolute;
    left: 0; top: 293px;
    width: 100%; height: 30px;
    background: var(--brand-yellow);
    color: var(--white);
    font-size: 15px;
    text-align: center;
    line-height: 30px;
  }
</style>
</head>
<body>
  <section class="card card--front" aria-label="Business card front">
    <div class="accent-bar"></div>
    <div class="wordmark"><span class="wordmark__dot"></span>Kelvoria</div>
    <div class="contact-panel">
      <p class="contact-panel__name">TOMAS BILBREA</p>
      <p class="contact-panel__role">MANAGING DIRECTOR</p>
      <ul class="contact-list">
        <li>
          <svg viewBox="0 0 16 16" aria-hidden="true"><path d="M3.5 1l3 3-1.7 2a9 9 0 0 0 5.2 5.2l2-1.7 3 3-2 2.2C7 14.5 1.5 9 1.3 3z"/></svg>
          +61 491058264
        </li>
        <li>
          <svg viewBox="0 0 16 16" aria-hidden="true"><path d="M1 3h14v10H1z M1 3l7 6 7-6" stroke="#105d3e" stroke-width="1.2"/></svg>
          tomas@kelvarin.com.au
        </li>
        <li>
          <svg viewBox="0 0 16 16" aria-hidden="true"><circle cx="8" cy="8" r="7"/><path d="M4 6c2 0 2 2 4 2s1 3 2 4M9 2c0 2 3 2 4 4" stroke="#105d3e" stroke-width="1.3" fill="none"/></svg>
          www.kelvoria.com.au
        </li>
        <li>
          <svg viewBox="0 0 16 16" aria-hidden="true"><path d="M8 0a5.5 5.5 0 0 0-5.5 5.5C2.5 10 8 16 8 16s5.5-6 5.5-10.5A5.5 5.5 0 0 0 8 0zm0 8a2.5 2.5 0 1 1 0-5 2.5 2.5 0 0 1 0 5z"/></svg>
          Melbourne, Australia
        </li>
      </ul>
    </div>
  </section>

  <section class="card card--back" aria-label="Business card back">
    <div class="wordmark"><span class="wordmark__dot"></span>Kelvoria</div>
    <div class="tagline-band">Hacemos más por ti!</div>
  </section>
</body>
</html>
```